International Reinsurance Business Platform Needs a PowerPoint Design

We need a powerpoint design for a new company based in Bermuda. We have created a platform to facilitate the incorporation and creation of off-shore reinsurance companies, primarily offered to asset managers to generate permanent capital at a fraction of the costs typically required by such a venture. We have no preference as to the color scheme, but would like for the final design to communicate professionalism, simplicity and elegance.
We have uploaded a very rudimentary draft (far from what we want), and welcome you to recreate a single page from it (it can be a combination of two pages into one; preferably something complicated enough to showcase the potential of your idea). From there, we will pick from the better submissions (of that single page) and work from there.
High-income asset managers
Business

```html
<!DOCTYPE html>
<html lang="en">
<head>
<meta charset="utf-8">
<title>Each faced significant hurdles</title>
<link rel="stylesheet" href="https://fonts.googleapis.com/css2?family=Carlito:ital,wght@0,400;0,700;1,400;1,700&display=swap">
<style>
  :root {
    --brand-blue: #0a98e6;
    --accent-blue: #1479e0;
    --icon-blue: #1565c8;
    --accent-yellow: #f6cf2a;
    --ink: #1b1b24;
    --white: #ffffff;
    --texture: #eef1f4;
  }
  html, body {
    margin: 0;
    padding: 0;
    width: 1200px;
    height: 900px;
    overflow: hidden;
    background: var(--white);
  }
  .slide {
    position: relative;
    width: 1200px;
    height: 900px;
    overflow: hidden;
    font-family: "Carlito", "Calibri", sans-serif;
    color: var(--ink);
    background: var(--white);
  }
  .slide-header {
    position: absolute;
    left: 0; top: 0;
    width: 1200px;
    height: 117px;
    background: var(--brand-blue);
  }
  .slide-title {
    position: absolute;
    left: 54px;
    top: 38px;
    margin: 0;
    font-size: 33px;
    font-weight: 700;
    color: var(--white);
  }
  .brand-name {
    position: absolute;
    right: 34px;
    top: 24px;
    font-size: 60px;
    font-weight: 400;
    letter-spacing: 1px;
    color: var(--white);
  }
  .background-texture {
    position: absolute;
    left: 420px; top: 117px;
    width: 780px; height: 687px;
    background: radial-gradient(ellipse at 75% 35%, var(--texture) 0%, rgba(238,241,244,0.5) 40%, rgba(255,255,255,0) 72%);
  }
  .hurdle-list {
    position: absolute;
    left: 0; top: 0;
    margin: 0; padding: 0;
    list-style: none;
  }
  .hurdle {
    position: absolute;
    left: 52px;
    display: flex;
    align-items: center;
    height: 48px;
    white-space: nowrap;
    font-size: 28px;
    font-weight: 700;
  }
  .hurdle-icon {
    width: 46px; height: 46px;
    margin-right: 28px;
    flex: none;
  }
  .emphasis {
    color: var(--accent-blue);
    font-style: italic;
    font-weight: 400;
    font-size: 34px;
    margin: 0 6px 0 2px;
  }
  .hurdle .emphasis:first-child { margin-left: 0; }
  .conclusion {
    position: absolute;
    left: 126px;
    top: 683px;
    margin: 0;
    font-size: 47px;
    font-weight: 400;
    color: var(--accent-blue);
  }
  .footer-rule {
    position: absolute;
    left: 0; top: 804px;
    width: 1200px; height: 8px;
    background: var(--accent-yellow);
  }
  .slide-footer {
    position: absolute;
    left: 0; top: 812px;
    width: 1200px; height: 88px;
    background: var(--brand-blue);
  }
  .page-number {
    position: absolute;
    right: 48px;
    top: 30px;
    font-size: 26px;
    font-weight: 700;
    color: var(--white);
  }
</style>
</head>
<body>
<div class="slide">
  <header class="slide-header">
    <h1 class="slide-title">Each faced significant hurdles</h1>
    <div class="brand-name">Harbourline Capital</div>
  </header>

  <div class="background-texture" role="img" aria-label="Faint grey dotted texture fading across the right side of the slide"></div>

  <svg width="0" height="0" style="position:absolute">
    <defs>
      <symbol id="arrow-badge" viewBox="0 0 46 46">
        <circle cx="23" cy="24" r="21" fill="#000" opacity="0.18"/>
        <circle cx="23" cy="23" r="21" fill="#ffffff"/>
        <circle cx="23" cy="23" r="16.5" fill="#1565c8"/>
        <path d="M14 23 H30 M24 17 L30 23 L24 29" fill="none" stroke="#ffffff" stroke-width="3" stroke-linecap="round" stroke-linejoin="round"/>
      </symbol>
    </defs>
  </svg>

  <ul class="hurdle-list">
    <li class="hurdle" style="top:219px"><svg class="hurdle-icon"><use href="#arrow-badge"/></svg>Had to hire marquee reinsurance teams</li>
    <li class="hurdle" style="top:308px"><svg class="hurdle-icon"><use href="#arrow-badge"/></svg>Reinsurace teams received <span class="emphasis">&nbsp;large</span>guarantees</li>
    <li class="hurdle" style="top:397px"><svg class="hurdle-icon"><use href="#arrow-badge"/></svg>Had to raise <span class="emphasis">&nbsp;at least</span>$250 million of capital</li>
    <li class="hurdle" style="top:486px"><svg class="hurdle-icon"><use href="#arrow-badge"/></svg><span class="emphasis">Large</span>busted deal, startup, and fixed costs</li>
    <li class="hurdle" style="top:575px"><svg class="hurdle-icon"><use href="#arrow-badge"/></svg>Redirection of resources for <span class="emphasis">&nbsp;1 to 2 year</span></li>
  </ul>

  <p class="conclusion">Many more have tried and failed</p>

  <div class="footer-rule"></div>
  <footer class="slide-footer">
    <span class="page-number">2</span>
  </footer>
</div>
</body>
</html>
```